WTF!!! We need a modern professional website for a business litigation law firm.

We need a modern, clean, professional and uncomplicated website for a new business trial and litigation law firm called "Haverlock Trial Firm PLLC". Website must be mobile optimized for iPad and smartphone. The law firm specializes in counseling and representing large corporations, small businesses and entrepreneurs in and out of the courtroom. Lawyers in the firm serve as Florida counsel and trial counsel to organizations facing claims involving product liability, premises liability, professional liability, vehicle and transportation liability, warranty claims, construction defects and delay claims, complex business disputes, commercial litigation and bid disputes in State and Federal Courts. The website is mainly to provide information about the firm, and should include sections describing the firm, identifying the Industries Served and Areas of Practice ," a separate page identifying the "Professionals", a separate page for "Resources & Advisories," and a traveling "Connect With Us" button a site visitor can click on that will launch an email to the Firm's general email account. The website should allow us to easily modify the content on these pages, and let us add/modify links to external information sources. We will not sell anything or take payments through the website. We do need to be able to easily upload and update photographs of attorneys and add new attorneys names/email hyperlinks as the firm grows. We would like to add developments in the law or success stories easily and quickly, such as through a blog page. On the "Connect With Us" page the website should have hyperlinks to email the Firm, and there should be hyperlinks to email each professional on the "Professionals" page. The website should be viewable on mobile devices without distortion. The law firm focuses on trial work and should have some imagery associated with courtrooms, but the overall theme of the site should be modern, clean, and communicate sophistication and strength. The website should be made in Wordpress. We have uploaded logo files for Haverlock Trial Firm.

Target Market(s)

Corporations and companies that are looking for legal representation. Other attorneys/legal industry.

Industry/Entity Type

Legal Industry

Coding

Coded - Design and coding required

Number of Pages Required

1 page

Font styles to use
Sans Serif

Requirements
Must have
• Simple, clean, sophisticated, modern website that includes the logo, watermark of logo, and the elements described above.
Nice to have
• Pictures of city scape, buildings, courtroom, team members.

```html
<!DOCTYPE html>
<html lang="en">
<head>
<meta charset="utf-8">
<title>Haverlock Trial Firm PLLC</title>
<link href="https://fonts.googleapis.com/css2?family=Montserrat:ital,wght@0,300;0,400;0,500;0,600;0,700;1,400&display=swap" rel="stylesheet">
<style>
:root{
  --black:#000;
  --ink:#111;
  --white:#fff;
  --grey-bg:#efefef;
  --card-grey:#e4e4e4;
  --text-grey:#555;
  --muted:#777;
  --footer:#9d9d9d;
  --blog-bg:#1b1b1b;
  --star:#e8491d;
}
*{margin:0;padding:0;box-sizing:border-box}
html,body{width:1200px;height:4428px;overflow:hidden}
body{font-family:"Montserrat",sans-serif;color:var(--ink);background:var(--white);position:relative}
.abs{position:absolute}
a{color:inherit;text-decoration:none}

/* hero */
.hero{left:0;top:0;width:1200px;height:638px;background:linear-gradient(100deg,#1a1410 0%,#3a2a1c 35%,#5c4229 55%,#2a1f16 80%,#140f0b 100%)}
.hero-side{left:0;top:0;width:96px;height:584px;background:var(--black)}
.brand{left:110px;top:22px;color:var(--white);font-weight:700;font-size:19px;letter-spacing:.5px;line-height:1.05;text-align:center}
.brand small{display:block;font-size:9px;letter-spacing:2px;font-weight:700}
.nav{left:244px;top:48px;display:flex;gap:17px;font-size:12.5px;color:#bdb4aa}
.nav .active{color:var(--white)}
.connect{left:946px;top:40px;border:1.5px solid var(--white);border-radius:20px;color:var(--white);font-size:12.5px;font-weight:500;padding:10px 15px}
.hero-title{left:110px;top:168px;color:var(--white);font-weight:700;font-size:90px;line-height:1}
.hero-sub{left:112px;top:272px;color:var(--white);font-weight:300;font-size:42px}
.hero-tag{left:112px;top:333px;color:var(--white);font-size:14.5px}
.hero-btn{left:112px;top:376px;border:1.5px solid var(--white);border-radius:20px;color:var(--white);font-size:14.5px;font-weight:500;padding:8px 18px}
.pager{left:0;top:584px;width:358px;height:54px;background:var(--white);display:flex;align-items:center;padding-left:112px;gap:16px;font-size:15px}
.pager b{font-size:32px;font-weight:600}
.pager span{display:flex;align-items:center;gap:6px}

/* shared section heads */
.eyebrow{font-size:20px;color:var(--text-grey);font-weight:400;letter-spacing:.5px}
.h2{font-size:38px;font-weight:600;letter-spacing:.5px}
.center{left:0;width:1200px;text-align:center}

/* about */
.about-head{left:112px;top:790px;font-size:38px;font-weight:600;line-height:60px;letter-spacing:.5px}
.about-frame{left:81px;top:1080px;width:466px;height:232px;border:1.5px solid #555}
.about-img{left:112px;top:983px;width:476px;height:298px;background:linear-gradient(170deg,#a9c7e2 0%,#b4c0c8 30%,#4f7c6a 50%,#2f6d8a 65%,#3f6a3a 85%,#2e4a2a 100%)}
.bullets{left:641px;top:780px;width:420px;list-style:none}
.bullets li{position:relative;padding-left:22px;font-size:15px;line-height:23px;color:var(--muted);margin-bottom:18px}
.bullets li::before{content:"";position:absolute;left:0;top:6px;width:11px;height:11px;border-radius:50%;background:#333}
.btn-dark{left:662px;top:1228px;width:124px;height:36px;border-radius:18px;background:var(--black);color:var(--white);font-size:14px;display:flex;align-items:center;justify-content:center}

/* practice */
.practice{left:0;top:1487px;width:1200px;height:453px;display:flex}
.pcard{width:300px;height:453px;position:relative;color:var(--white)}
.pcard .vlabel{position:absolute;left:22px;top:190px;transform:rotate(-90deg);transform-origin:left top;font-size:16px;white-space:nowrap;top:190px}
.pcard .vline{position:absolute;left:32px;top:250px;width:1.5px;height:70px;background:var(--white)}
.pcard h3{position:absolute;left:30px;top:365px;font-size:20px;font-weight:600;line-height:22px}
.pcard .more{position:absolute;left:30px;top:418px;font-size:14.5px;color:#ddd}
.p1{background:linear-gradient(160deg,#2b2b2b,#5a5855 60%,#3a3836)}
.p2{background:linear-gradient(160deg,#2e4a5c,#4f6b7c 55%,#2d4150)}
.p3{background:linear-gradient(160deg,#5a4a3a,#a0702a 50%,#6b5640)}
.p4{background:linear-gradient(160deg,#4a3c32,#8a7a6a 55%,#5a4e44)}
.arrow{width:46px;height:46px;border-radius:50%;background:var(--black);top:1679px;display:flex;align-items:center;justify-content:center}

/* industries */
.ind-bg{left:0;top:1940px}
.ind{top:2146px;width:190px;text-align:center;font-size:17px;font-weight:600;line-height:22px}
.ind svg{display:block;margin:0 auto 22px}

/* reviews */
.review{width:306px;padding:24px 22px;background:var(--card-grey);color:#333}
.review.dark{background:var(--black);color:var(--white)}
.review .name{font-size:17px}
.review .stars{color:var(--star);font-size:19px;letter-spacing:5px;margin:6px 0 12px}
.review p{font-style:italic;font-size:17px;line-height:26px;color:#555}
.review.dark p{color:#ddd}
.review .quote{position:absolute;right:22px;top:16px;font-size:110px;font-weight:700;line-height:1;color:#cfcfcf;font-family:Georgia,serif}
.review.dark .quote{color:var(--white)}

/* blog */
.blog{left:0;top:3249px;width:1200px;height:708px;background:var(--blog-bg)}
.post{top:3438px;width:399px;color:var(--white)}
.post .img{height:232px}
.post .vl{position:absolute;left:31px;top:181px;width:1.5px;height:89px;background:var(--white)}
.post h4{margin:20px 0 0 58px;font-size:22px;font-weight:500}
.post p{margin:12px 0 0 60px;font-size:12px;line-height:22px;color:#ccc;width:320px}
.slider{left:110px;top:3850px;width:978px;height:2px;background:#555}
.slider i{position:absolute;left:438px;top:0;width:540px;height:2px;background:var(--white)}

/* footer */
.footer{left:0;top:3957px;width:1200px;height:471px;background:var(--footer)}
.f-brand{left:112px;top:4140px;font-size:58px;font-weight:700;color:var(--black);line-height:1;text-align:center;letter-spacing:1px}
.f-brand span{display:block;font-size:27px;letter-spacing:6px;margin-top:6px}
.f-head{font-size:20px;font-weight:600;color:var(--black)}
.f-links{left:496px;top:4096px;list-style:none;font-size:15px;line-height:25.7px;color:#222}
.f-contact{left:729px;top:4100px;width:360px}
.f-contact div{display:flex;gap:14px;font-size:15px;line-height:22px;color:#222;margin-bottom:24px}
.f-contact svg{flex:none}
.copy{left:0;top:4369px;width:1200px;text-align:center;font-size:14.5px;color:#222}
</style>
</head>
<body>

<!-- Hero -->
<div class="abs hero" role="img" aria-label="Courtroom scene with an attorney addressing a judge"></div>
<div class="abs hero-side"></div>
<div class="abs brand">HAVERLOCK<small>TRIAL FIRM</small></div>
<nav class="abs nav">
  <a class="active">Home</a><a>About Us</a><a>Areas of Practice</a><a>Industries Served</a><a>Professionals</a><a>Resources &amp; Advisories</a><a>Blog</a>
</nav>
<a class="abs connect">Connect With Us</a>
<h1 class="abs hero-title">Haverlock</h1>
<div class="abs hero-sub">Trial Firm PLLC</div>
<p class="abs hero-tag">Protecting your business through trial excellence.</p>
<a class="abs hero-btn">Request a Consultation</a>
<div class="abs pager">
  <b>01</b>
  <span><svg width="26" height="16" viewBox="0 0 26 16"><path d="M25 8H2M8 2L2 8l6 6" fill="none" stroke="#111" stroke-width="2"/></svg>Pre</span>
  <span style="margin-left:10px">Next<svg width="26" height="16" viewBox="0 0 26 16"><path d="M1 8h23M18 2l6 6-6 6" fill="none" stroke="#111" stroke-width="2"/></svg></span>
</div>

<!-- About -->
<div class="abs eyebrow" style="left:112px;top:740px">ABOUT HAVERLOCK TRIAL FIRM PLLC</div>
<h2 class="abs about-head">EMPHASIZE STRENGTHS<br>SUCH AS EXPERIENCE,<br>RESULTS</h2>
<div class="abs about-frame"></div>
<div class="abs about-img" role="img" aria-label="Aerial view of a city skyline beside a lake"></div>
<ul class="abs bullets">
  <li>Sed ut perspiciatis unde omnis iste natus error sit voluptatem accusantium doloremque laudantium, totam rem aperiam explicabo.</li>
  <li>Sed ut perspiciatis unde omnis iste natus error sit voluptatem accusantium doloremque laudantium, totam rem aperiam explicabo.</li>
  <li>Sed ut perspiciatis unde omnis iste natus error sit voluptatem accusantium doloremque laudantium, totam rem aperiam explicabo.</li>
  <li>Sed ut perspiciatis unde omnis iste natus error sit voluptatem accusantium doloremque laudantium, totam rem aperiam explicabo.</li>
  <li>Sed ut perspiciatis unde omnis iste natus error sit voluptatem accusantium doloremque laudantium, totam rem aperiam explicabo.</li>
</ul>
<a class="abs btn-dark">Read More</a>

<!-- Areas of practice -->
<div class="abs center eyebrow" style="top:1372px">OUR SERVICES</div>
<h2 class="abs center h2" style="top:1412px">AREAS OF PRACTICE</h2>
<div class="abs practice">
  <div class="pcard p1" role="img" aria-label="Hands working at a desk with a calculator"><span class="vlabel">Product Liability</span><i class="vline"></i><h3>PRODUCT LIABILITY</h3><span class="more">Read More</span></div>
  <div class="pcard p2" role="img" aria-label="Glasses resting on financial charts"><span class="vlabel">Premises Liability</span><i class="vline"></i><h3>PREMISES LIABILITY</h3><span class="more">Read More</span></div>
  <div class="pcard p3" role="img" aria-label="Shield with an umbrella and check mark"><span class="vlabel">Product Liability</span><i class="vline"></i><h3>WARRANTY CLAIMS</h3><span class="more">Read More</span></div>
  <div class="pcard p4" role="img" aria-label="Professional signing documents in an office"><span class="vlabel">Professional Liability</span><i class="vline"></i><h3>PROFESSIONAL<br>LIABILITY</h3><span class="more">Read More</span></div>
</div>
<div class="abs arrow" style="left:61px"><svg width="16" height="18" viewBox="0 0 16 18"><path d="M11 2L4 9l7 7" fill="none" stroke="#fff" stroke-width="3"/></svg></div>
<div class="abs arrow" style="left:1089px"><svg width="16" height="18" viewBox="0 0 16 18"><path d="M5 2l7 7-7 7" fill="none" stroke="#fff" stroke-width="3"/></svg></div>

<!-- Industries -->
<svg class="abs ind-bg" width="1200" height="490" viewBox="0 0 1200 490"><path d="M0 0H1200V394L600 489L0 394Z" fill="#efefef"/></svg>
<div class="abs center eyebrow" style="top:2022px">INDUSTRIES</div>
<h2 class="abs center h2" style="top:2060px">INDUSTRIES SERVED</h2>
<div class="abs ind" style="left:111px"><svg width="100" height="112" viewBox="0 0 100 112"><path d="M50 2L97 29V83L50 110L3 83V29Z" fill="none" stroke="#000" stroke-width="3"/><path d="M50 10L90 33V79L50 102L10 79V33Z" fill="#000"/><circle cx="50" cy="46" r="9" fill="none" stroke="#fff" stroke-width="2.5"/><path d="M32 74c2-12 10-16 18-16s16 4 18 16" fill="none" stroke="#fff" stroke-width="2.5"/></svg>Corporate<br>Sector</div>
<div class="abs ind" style="left:306px"><svg width="100" height="112" viewBox="0 0 100 112"><path d="M50 2L97 29V83L50 110L3 83V29Z" fill="none" stroke="#000" stroke-width="3"/><path d="M50 10L90 33V79L50 102L10 79V33Z" fill="#000"/><path d="M28 52l12-8 10 6 10-6 12 8-14 16H42Z" fill="none" stroke="#fff" stroke-width="2.5"/></svg>Small Business &amp;<br>Entrepreneurs</div>
<div class="abs ind" style="left:502px"><svg width="100" height="112" viewBox="0 0 100 112"><path d="M50 2L97 29V83L50 110L3 83V29Z" fill="none" stroke="#000" stroke-width="3"/><path d="M50 10L90 33V79L50 102L10 79V33Z" fill="#000"/><path d="M30 70h40M34 70V58h32v12M34 64h32M42 58v12M58 58v12M60 58l8-18" fill="none" stroke="#fff" stroke-width="2.5"/></svg>Construction &amp;<br>Real Estate</div>
<div class="abs ind" style="left:698px"><svg width="100" height="112" viewBox="0 0 100 112"><path d="M50 2L97 29V83L50 110L3 83V29Z" fill="none" stroke="#000" stroke-width="3"/><path d="M50 10L90 33V79L50 102L10 79V33Z" fill="#000"/><circle cx="50" cy="56" r="20" fill="none" stroke="#fff" stroke-width="2.5"/><rect x="38" y="46" width="9" height="9" fill="none" stroke="#fff" stroke-width="2"/><rect x="53" y="46" width="9" height="9" fill="none" stroke="#fff" stroke-width="2"/><rect x="38" y="59" width="9" height="9" fill="none" stroke="#fff" stroke-width="2"/><rect x="53" y="59" width="9" height="9" fill="none" stroke="#fff" stroke-width="2"/></svg>Transportation &amp;<br>Logistics</div>
<div class="abs ind" style="left:893px"><svg width="100" height="112" viewBox="0 0 100 112"><path d="M50 2L97 29V83L50 110L3 83V29Z" fill="none" stroke="#000" stroke-width="3"/><path d="M50 10L90 33V79L50 102L10 79V33Z" fill="#000"/><path d="M50 38l16 9v18l-16 9-16-9V47Z M34 47l16 9 16-9 M50 56v18" fill="none" stroke="#fff" stroke-width="2.5"/></svg>Product<br>Development</div>

<!-- Reviews -->
<div class="abs center eyebrow" style="top:2543px">TESTIMONIAL</div>
<h2 class="abs center h2" style="top:2580px">CLIENT REVIEWS</h2>
<div class="abs review" style="left:110px;top:2680px;height:409px"><span class="quote">”</span><div class="name">Jhone Deo</div><div class="stars">★★★★★</div><p>Lorem ipsum dolor sit amet, consectetur adipiscing elit, sed do eiusmod tempor incididunt ut labore et dolore magna aliqua. Ut enim ad minim veniam, quis nostrud exercitation ullamco laboris nisi ut aliquip ex ea commodo consequat. Duis aute irure dolor</p></div>
<div class="abs review dark" style="left:447px;top:2726px;height:410px"><span class="quote">”</span><div class="name">Jhone Deo</div><div class="stars">★★★★★</div><p>Lorem ipsum dolor sit amet, consectetur adipiscing elit, sed do eiusmod tempor incididunt ut labore et dolore magna aliqua. Ut enim ad minim veniam, quis nostrud exercitation ullamco laboris nisi ut aliquip ex ea commodo consequat. Duis aute irure dolor</p></div>
<div class="abs review" style="left:782px;top:2680px;height:409px"><span class="quote">”</span><div class="name">Jhone Deo</div><div class="stars">★★★★★</div><p>Lorem ipsum dolor sit amet, consectetur adipiscing elit, sed do eiusmod tempor incididunt ut labore et dolore magna aliqua. Ut enim ad minim veniam, quis nostrud exercitation ullamco laboris nisi ut aliquip ex ea commodo consequat. Duis aute irure dolor</p></div>

<!-- Blog -->
<div class="abs blog" role="img" aria-label="Dim courtroom backdrop"></div>
<div class="abs center eyebrow" style="top:3330px;color:#fff">BLOG</div>
<h2 class="abs center h2" style="top:3364px;color:#fff;font-weight:500">LATEST NEWS</h2>
<div class="abs post" style="left:110px"><div class="img" role="img" aria-label="Two attorneys reviewing papers in court" style="background:linear-gradient(135deg,#8a8a8a,#cfcfcf 50%,#6a6a6a)"></div><i class="vl"></i><h4>Nemo enim ipsam</h4><p>Lorem ipsum dolor sit amet, consectetur adipiscing elit, sed do eiusmod tempor incididunt ut labore et dolore magna aliqua.</p></div>
<div class="abs post" style="left:531px"><div class="img" role="img" aria-label="Empty courtroom interior" style="background:linear-gradient(180deg,#2a2a2a,#6a6a6a 55%,#1e1e1e)"></div><i class="vl"></i><h4>Duis aute irure dolor</h4><p>Lorem ipsum dolor sit amet, consectetur adipiscing elit, sed do eiusmod tempor incididunt ut labore et dolore magna aliqua.</p></div>
<div class="abs post" style="left:954px;width:246px;overflow:hidden"><div class="img" role="img" aria-label="Camera recording a courtroom session" style="background:linear-gradient(135deg,#3a3a3a,#8a8a8a 60%,#4a4a4a)"></div><i class="vl"></i><h4 style="white-space:nowrap">Excepteur sint occaecat</h4><p>Lorem ipsum dolor sit amet, consectetur adipiscing elit, sed do eiusmod tempor incididunt ut labore et dolore magna aliqua.</p></div>
<div class="abs slider"><i></i></div>

<!-- Footer -->
<div class="abs footer"></div>
<div class="abs f-brand">HAVERLOCK<span>TRIAL FIRM</span></div>
<div class="abs f-head" style="left:493px;top:4048px">QUICK LINKS</div>
<ul class="abs f-links">
  <li>Home</li><li>About Us</li><li>Areas of Practice</li><li>Industries Served</li><li>Professionals</li><li>Resources &amp;</li><li>Advisories</li><li>Blog</li><li>Contact Us</li>
</ul>
<div class="abs f-head" style="left:729px;top:4048px">GET IN TOUCH</div>
<div class="abs f-contact">
  <div><svg width="32" height="32" viewBox="0 0 32 32"><circle cx="16" cy="16" r="16" fill="#000"/><path d="M16 8a5 5 0 0 0-5 5c0 4 5 10 5 10s5-6 5-10a5 5 0 0 0-5-5z" fill="#fff"/><circle cx="16" cy="13" r="1.8" fill="#000"/></svg><span>1254 ipsum dolor sit amet, consectetur adipiscing elit 2548</span></div>
  <div style="align-items:center"><svg width="32" height="32" viewBox="0 0 32 32"><circle cx="16" cy="16" r="16" fill="#000"/><path d="M11 9l3 0 1.5 4-2 1.5a9 9 0 0 0 4 4l1.5-2 4 1.5v3c0 1-1 2-2 2C14 23 9 18 9 11c0-1 1-2 2-2z" fill="#fff"/></svg><span>+1 888-888-8888</span></div>
  <div style="align-items:center"><svg width="32" height="32" viewBox="0 0 32 32"><circle cx="16" cy="16" r="16" fill="#000"/><rect x="9" y="11" width="14" height="10" rx="1" fill="#fff"/><path d="M9 12l7 5 7-5" fill="none" stroke="#000" stroke-width="1.5"/></svg><span>info@haverlocktrialfirm.com</span></div>
</div>
<div class="abs copy">Copyrights 2025 Company Name All Rights Reserved</div>

</body>
</html>
```